NZ First of it's kind solutions directory and marketplace for busy Mums needs a business card design

We need a business card design for our new nationwide business in NZ (long term plans to go global). We provide solutions to the everyday challenges that busy Mums face by connecting them with quality communities and suppliers of carefully selected, relevant products and services. We sell direct via our online marketplace. The final design should communicate our values of inclusivity, quality and smart solutions. Colours should incorporate our logo colour palette of #477077 and #6ba8b2. Our website is at https://www.brightnestmums.example

Target Market(s)

busy Mums, Age 28 – 50, female, income over $100K, location main centres NZ primarily but NZ wide. Is likely juggling work or career with a young family. Probably had hobbies which have fallen by the wayside.
-Wants to succeed in her chosen career without compromising on family life
-to successfully juggle her career without feeling like she is compromising her children
- Is time poor, something always has to give and it’s generally her health (she’ll stay up late, get stressed)
- probably ex corporate or professional career. Has discretional income

Industry/Entity Type

Business

Contact Information for Business Card

Lena Forbisher, Founder, BrightNestMums.example (Strapline Tap; Gather; Sorted), 47 Kowhai Terrace, Ellerslie, Auckland 1051, New Zealand. Mob: 021 483 517 Ph: +64 (0)9 571 4860

Font styles to use
Other font styles liked:
• Raleway, and/or Architects Daughter

Colors
00a990
33b8a4
86cfc6
cfeae6

Requirements
Must have
• the above details, streamline. the logo and colours associated with those logos
Should not have
• foil or metallic colours

```html
<!DOCTYPE html>
<html lang="en">
<head>
<meta charset="utf-8">
<title>BrightNestMums business card</title>
<link rel="stylesheet" href="https://fonts.googleapis.com/css2?family=Roboto:wght@400;500&family=Roboto+Condensed:wght@700&display=swap">
<style>
  :root {
    --backdrop: #3b3b3d;
    --card: #262628;
    --brand-deep: #477077;
    --brand-light: #6ba8b2;
    --ink: #f2f2f2;
    --rule: #8a8a8a;
  }
  * { margin: 0; padding: 0; box-sizing: border-box; }
  html, body {
    width: 1200px; height: 900px; overflow: hidden;
    background: var(--backdrop);
    font-family: "Roboto", Arial, sans-serif;
  }
  .stage { position: relative; width: 1200px; height: 900px; }
  .card {
    position: absolute; left: 280px; width: 640px; height: 356px;
    background: var(--card);
    box-shadow: 0 6px 18px rgba(0,0,0,0.35);
  }
  .card--front { top: 74px; }
  .card--back { top: 470px; }

  /* front */
  .wordmark {
    position: absolute; top: 120px; left: 0; right: 0;
    display: flex; align-items: center; justify-content: center; gap: 14px;
  }
  .wordmark__dot {
    width: 34px; height: 34px; border-radius: 50%;
    background: var(--brand-light);
  }
  .wordmark__name {
    font-family: "Roboto", Arial, sans-serif;
    font-weight: 500; font-size: 44px; letter-spacing: -0.5px;
    color: var(--brand-light);
  }
  .strapline {
    position: absolute; top: 236px; left: 0; right: 0;
    text-align: center; font-size: 15px; color: var(--ink);
  }

  /* back */
  .identity {
    position: absolute; top: 108px; right: 352px; text-align: right;
  }
  .identity__name {
    font-family: "Roboto Condensed", "Arial Narrow", sans-serif;
    font-weight: 700; font-size: 38px; line-height: 1;
    color: var(--brand-light); letter-spacing: 0.5px;
  }
  .identity__role {
    margin-top: 4px;
    font-size: 17px; font-weight: 500; letter-spacing: 1px;
    color: var(--brand-light);
  }
  .divider {
    position: absolute; top: 96px; left: 304px;
    width: 1.5px; height: 86px; background: var(--rule);
  }
  .contacts {
    position: absolute; top: 104px; left: 326px;
    list-style: none;
  }
  .contacts__item {
    display: flex; align-items: center; gap: 10px;
    font-size: 17px; line-height: 24px; color: var(--ink);
  }
  .contacts__icon { width: 14px; height: 14px; flex: none; }
  .address {
    position: absolute; top: 262px; left: 40px;
    display: flex; align-items: center; gap: 8px;
    font-size: 18px; color: var(--ink);
  }
  .address__icon { width: 14px; height: 18px; }
</style>
</head>
<body>
<main class="stage">
  <section class="card card--front">
    <div class="wordmark">
      <span class="wordmark__dot"></span>
      <span class="wordmark__name">BrightNestMums</span>
    </div>
    <p class="strapline">Tap; Gather; Sorted</p>
  </section>

  <section class="card card--back">
    <div class="identity">
      <h1 class="identity__name">LENA FORBISHER</h1>
      <p class="identity__role">FOUNDER</p>
    </div>
    <span class="divider"></span>
    <ul class="contacts">
      <li class="contacts__item">
        <svg class="contacts__icon" viewBox="0 0 14 14" aria-hidden="true"><path d="M3 1 L5.5 1 L6.5 4 L5 5.2 C5.8 7 7 8.2 8.8 9 L10 7.5 L13 8.5 L13 11 C13 12 12 13 11 13 C5.5 12.6 1.4 8.5 1 3 C1 2 2 1 3 1 Z" fill="var(--brand-light)"/></svg>
        <span>+64 (0)9 571 4860</span>
      </li>
      <li class="contacts__item">
        <svg class="contacts__icon" viewBox="0 0 14 14" aria-hidden="true"><rect x="3" y="0.8" width="8" height="12.4" rx="1.5" fill="none" stroke="var(--brand-light)" stroke-width="1.6"/><circle cx="7" cy="10.8" r="0.9" fill="var(--brand-light)"/></svg>
        <span>021 483 517</span>
      </li>
      <li class="contacts__item">
        <svg class="contacts__icon" viewBox="0 0 14 14" aria-hidden="true"><circle cx="7" cy="7" r="6.2" fill="var(--brand-light)"/><path d="M2 6 C4 5 5 7 7 6 C8 5 9 3 11 4" fill="none" stroke="var(--card)" stroke-width="1.3"/></svg>
        <span>BrightNestMums.example</span>
      </li>
    </ul>
    <p class="address">
      <svg class="address__icon" viewBox="0 0 14 18" aria-hidden="true"><path d="M7 1 C3.7 1 1.2 3.5 1.2 6.7 C1.2 10.7 7 17 7 17 C7 17 12.8 10.7 12.8 6.7 C12.8 3.5 10.3 1 7 1 Z" fill="var(--brand-light)"/><circle cx="7" cy="6.6" r="2.2" fill="var(--card)"/></svg>
      <span>47 Kowhai Terrace, Ellerslie, Auckland 1051, New Zealand.</span>
    </p>
  </section>
</main>
</body>
</html>
```